£500 POUND FOR A4 8 page booklet

to take 4 of my already done leaflet and make one a4 8 page booklet. The colour themes are green for fenn moor bespoke timber frame and red for the rest. The front page needs to be the sarrowcoat fluid followed by another two pages of it www.sarrowcoatfluid.co.uk. then two pages of fenn moor then two pages of dune crest then 1 page of spray protection (making sure you mention tower blocks in london )www.dune-crest.co.uk and www.fenn-moor.co.uk
i need the booklet to look way more professional than what these flyers are (grown up ) i can give more information kevin@harlowjoinery.com
construction

```html
<!DOCTYPE html>
<html lang="en">
<head>
<meta charset="utf-8">
<title>Dune Crest – Back Cover</title>
<link rel="stylesheet" href="https://fonts.googleapis.com/css2?family=Arimo:wght@400&family=Tinos:wght@400&display=swap">
<style>
  :root {
    --backdrop: #3d3d3d;
    --brand-blue: #4a8fd0;
    --brand-blue-light: #6aa6dc;
    --ink-white: #ffffff;
    --photo-grey: #9aa4ae;
    --photo-blue: #4d7fae;
  }
  * { box-sizing: border-box; margin: 0; padding: 0; }
  html, body { width: 1200px; height: 941px; overflow: hidden; background: var(--backdrop); }
  .back-cover {
    position: absolute; left: 289px; top: 30px; width: 622px; height: 880px;
    background: var(--brand-blue); overflow: hidden;
    font-family: "Arimo", Arial, sans-serif; color: var(--ink-white);
  }
  .back-cover__swirls { position: absolute; inset: 0; }
  .intro-box {
    position: absolute; left: 62px; top: 96px; width: 498px; height: 150px;
    border: 1px solid rgba(255,255,255,0.85);
    display: flex; align-items: center; justify-content: center;
    padding: 0 24px; text-align: center;
    font-size: 14.5px; line-height: 1.35; letter-spacing: 0.2px;
  }
  .hero-photo {
    position: absolute; left: 0; top: 300px; width: 622px; height: 270px;
    background: linear-gradient(100deg, var(--photo-grey) 0%, #c9ced3 35%, var(--photo-blue) 60%, #6f9ac2 100%);
  }
  .social-links { position: absolute; right: 34px; top: 604px; display: flex; gap: 8px; }
  .social-links span { width: 20px; height: 20px; background: var(--ink-white); border-radius: 2px; }
  .contact-heading {
    position: absolute; left: 34px; top: 608px;
    font-family: "Tinos", "Times New Roman", serif; font-size: 32px; line-height: 1;
  }
  .contact-rule { position: absolute; left: 34px; right: 0; top: 650px; height: 3px; background: var(--ink-white); }
  .contact-item { position: absolute; display: flex; align-items: flex-start; gap: 14px; font-size: 13px; line-height: 1.3; }
  .contact-item svg { flex: none; }
  .contact-item--address { left: 34px; top: 676px; width: 320px; }
  .contact-item--phone { left: 34px; top: 748px; }
  .contact-item--email { left: 376px; top: 676px; }
  .contact-item--web { left: 376px; top: 726px; }
  .contact-item p { padding-top: 3px; }
</style>
</head>
<body>
  <main class="back-cover">
    <svg class="back-cover__swirls" width="622" height="880" aria-hidden="true">
      <path d="M-40 120 C 180 40, 420 40, 680 160" fill="none" stroke="var(--brand-blue-light)" stroke-width="40" opacity="0.25"/>
      <path d="M-40 820 C 200 700, 460 700, 680 800" fill="none" stroke="var(--brand-blue-light)" stroke-width="50" opacity="0.2"/>
    </svg>

    <section class="intro-box">
      <p>Dune Crest are a specialist Roof Renovation and Insulation Company that provide a fast and cost effective service for roofing renovation, roof insulation for domestic and commercial roofs.</p>
    </section>

    <div class="hero-photo" role="img" aria-label="Photo of a gloved hand dipping a paintbrush into a tin of blue liquid roof coating"></div>

    <div class="social-links" aria-label="Social media links"><span></span><span></span><span></span></div>

    <h2 class="contact-heading">Contact Us</h2>
    <div class="contact-rule"></div>

    <div class="contact-item contact-item--address">
      <svg width="26" height="26" viewBox="0 0 26 26" aria-hidden="true"><circle cx="13" cy="13" r="12" fill="none" stroke="#fff" stroke-width="1.5"/><path d="M13 6a4.5 4.5 0 0 0-4.5 4.5C8.5 14 13 20 13 20s4.5-6 4.5-9.5A4.5 4.5 0 0 0 13 6z" fill="#fff"/><circle cx="13" cy="10.5" r="1.8" fill="var(--brand-blue)"/></svg>
      <p>Unit 4b, The Old Kilnworks, Marsh Lane, Elmbridge Green, Bedfordshire, SG21 7QT, United Kingdom</p>
    </div>
    <div class="contact-item contact-item--phone">
      <svg width="26" height="26" viewBox="0 0 26 26" aria-hidden="true"><circle cx="13" cy="13" r="12" fill="none" stroke="#fff" stroke-width="1.5"/><rect x="9.5" y="6.5" width="7" height="13" rx="1.2" fill="none" stroke="#fff" stroke-width="1.4"/><circle cx="13" cy="17.3" r="0.8" fill="#fff"/></svg>
      <p>01632 960418 or &nbsp;07700 900 612</p>
    </div>
    <div class="contact-item contact-item--email">
      <svg width="26" height="26" viewBox="0 0 26 26" aria-hidden="true"><circle cx="13" cy="13" r="12" fill="none" stroke="#fff" stroke-width="1.5"/><rect x="7" y="9" width="12" height="8" fill="#fff"/><path d="M7 9l6 4.5L19 9" fill="none" stroke="var(--brand-blue)" stroke-width="1.2"/></svg>
      <p>info@dune-crest.co.uk</p>
    </div>
    <div class="contact-item contact-item--web">
      <svg width="26" height="26" viewBox="0 0 26 26" aria-hidden="true"><circle cx="13" cy="13" r="12" fill="none" stroke="#fff" stroke-width="1.5"/><circle cx="13" cy="13" r="6.5" fill="none" stroke="#fff" stroke-width="1.2"/><ellipse cx="13" cy="13" rx="2.8" ry="6.5" fill="none" stroke="#fff" stroke-width="1.1"/><path d="M6.5 13h13M7.5 10h11M7.5 16h11" stroke="#fff" stroke-width="1"/></svg>
      <p>www.sarrowcoatfluid.co.uk</p>
    </div>
  </main>
</body>
</html>
```